Business card for Eyelash extension salon in Marlow Hills,California USA

We need new business card for our salon in Marlow Hills. The salon name is 'Lashvera' . We would like to have...Business name: Lashvera Name of person: will provide later Address 4720 N.Alder Crest Ave Marlow Hills , CA 90299 Phone: will provide later (Text only) Web: www.lashverastudio.example Snapgrid icon, Circlebook icon follow us for seasonal campaign and news @lashverastudiolounge Design should look elegant, high-end, clean, simple, cohesive with my brand. Please refer my brand board. Business name color will be metallic bronzy color. Im thinking grey background or white background. Thanks

Target Market(s)

25-35. Gender neutral. People who are in Entertainment business industry.
This is High-end Eyelash extension salon in Marlow Hills

Industry/Entity Type

Beauty Salon

Contact Information for Business Card

Business name: Lashvera
Name of person: will provide later
Address 4720 N.Alder Crest Ave Marlow Hills , CA 90299
Phone: will provide later (Text only)
Web: www.lashverastudio.example
Snapgrid icon, Circlebook icon
follow us for seasonal campaign and news @lashverastudiolounge

Requirements
Must have
• Beautiful, elegant, clean and simple look but very attractive and modern
Should not have
• We don't like too clutter, too busy designs.

```html
<!DOCTYPE html>
<html lang="en">
<head>
<meta charset="utf-8">
<title>Lashvera — Business Card</title>
<link href="https://fonts.googleapis.com/css2?family=Libre+Baskerville:wght@400;700&display=swap" rel="stylesheet">
<style>
  :root {
    --backdrop: #e9e4dc;
    --ink: #141414;
    --marble-light: #fbfbfb;
    --marble-mid: #e4e4e6;
    --marble-vein: #c9c9cd;
    --panel: rgba(255, 255, 255, 0.88);
    --shadow: rgba(60, 45, 30, 0.28);
  }
  * { box-sizing: border-box; margin: 0; padding: 0; }
  html, body {
    width: 1200px; height: 995px; overflow: hidden;
    background: var(--backdrop);
    font-family: "Libre Baskerville", Georgia, serif;
    color: var(--ink);
  }
  .stage {
    position: relative; width: 1200px; height: 995px;
    display: flex; justify-content: center; align-items: center; gap: 70px;
  }
  .card {
    position: relative; width: 420px; height: 600px;
    border-radius: 26px; overflow: hidden;
    box-shadow: 0 14px 30px var(--shadow);
  }
  .card-marble {
    position: absolute; inset: 0;
    background:
      radial-gradient(ellipse at 12% 8%, var(--marble-vein) 0%, transparent 28%),
      radial-gradient(ellipse at 92% 45%, var(--marble-mid) 0%, transparent 30%),
      radial-gradient(ellipse at 20% 92%, var(--marble-vein) 0%, transparent 26%),
      linear-gradient(135deg, var(--marble-light), var(--marble-mid) 55%, var(--marble-light));
  }
  .card-panel {
    position: absolute; inset: 34px;
    border-radius: 22px;
    background: var(--panel);
  }
  .card-content {
    position: absolute; inset: 34px;
    display: flex; flex-direction: column; align-items: center;
    text-align: center;
  }
  .brand-name {
    font-size: 54px; font-weight: 400; letter-spacing: 1px; line-height: 1;
  }
  .website { font-size: 16px; font-weight: 700; letter-spacing: 0.6px; }

  .card--front .card-content { justify-content: center; padding-top: 20px; }
  .card--front .brand-name { margin-bottom: 46px; }

  .card--back .card-content { padding-top: 72px; }
  .card--back .brand-name { font-size: 48px; margin-bottom: 56px; }
  .person-name { font-size: 30px; font-weight: 700; line-height: 1; }
  .person-role { font-size: 15px; margin-top: 2px; margin-bottom: 22px; }
  .contact-line { font-size: 15px; line-height: 1.5; }
  .contact-line b { font-weight: 700; }
  .address { margin-top: 4px; }
  .social {
    display: flex; gap: 14px; margin-top: 18px; font-size: 12px;
  }
  .social-item { display: flex; align-items: center; gap: 5px; }
  .social-box { width: 14px; height: 14px; border: 1.5px solid var(--ink); border-radius: 2px; }
  .handle { font-size: 15px; margin-top: 8px; }
  .card--back .website { margin-top: auto; margin-bottom: 22px; }
</style>
</head>
<body>
<main class="stage">
  <article class="card card--front">
    <div class="card-marble" role="img" aria-label="White marble texture with soft grey veins"></div>
    <div class="card-panel"></div>
    <div class="card-content">
      <h1 class="brand-name">Lashvera</h1>
      <p class="website">www.lashverastudio.example</p>
    </div>
  </article>

  <article class="card card--back">
    <div class="card-marble" role="img" aria-label="White marble texture with soft grey veins"></div>
    <div class="card-panel"></div>
    <div class="card-content">
      <h2 class="brand-name">Lashvera</h2>
      <p class="person-name">Maren Ashby</p>
      <p class="person-role">Owner</p>
      <p class="contact-line"><b>P:</b> +1 310 555 0148</p>
      <p class="contact-line"><b>E:</b> hello@lashverastudio.example</p>
      <p class="contact-line address">4720 N.Alder Crest Ave Marlow Hills<br>CA 90299</p>
      <div class="social">
        <span class="social-item"><span class="social-box"></span>Circlebook</span>
        <span class="social-item"><span class="social-box"></span>Snapgrid</span>
      </div>
      <p class="handle">@lashverastudiolounge</p>
      <p class="website">www.lashverastudio.example</p>
    </div>
  </article>
</main>
</body>
</html>
```